Business card por a urban DJ, up scale audience target

Need a sober design, modern, conservative colors but i can consider some options, y play rnb, hip hop, EDM and top40.

Business card for contact and personal info, double sided, use logo attrached please; im 42 so i need a card acording to my age an target audience.

Target Market(s)

Adult people, up scale audience

Industry/Entity Type

Music Download

Contact Information for Business Card

Cel (318) 4207265518 www.lumadrift.com

Requirements
Must have
• open mind
Nice to have
• open mind
Should not have
• DJ

```html
<!DOCTYPE html>
<html lang="en">
<head>
<meta charset="utf-8">
<title>Lumadrift Business Card</title>
<link href="https://fonts.googleapis.com/css2?family=Arimo:wght@400;700&display=swap" rel="stylesheet">
<style>
  :root {
    --backdrop: #3a322e;
    --card: #141414;
    --ink: #ffffff;
    --ink-soft: #d9d9d9;
  }
  * { margin: 0; padding: 0; box-sizing: border-box; }
  html, body { width: 1200px; height: 780px; overflow: hidden; }
  body {
    background: var(--backdrop);
    font-family: "Arimo", Arial, sans-serif;
    color: var(--ink);
    display: flex;
    align-items: center;
    justify-content: center;
    gap: 40px;
  }
  .card {
    width: 540px;
    height: 309px;
    background: var(--card);
    border-radius: 4px;
    position: relative;
    box-shadow: 0 10px 30px rgba(0,0,0,0.45);
  }
  .brand-name {
    font-weight: 700;
    color: var(--ink);
    letter-spacing: 2px;
    line-height: 1;
  }
  /* Front side */
  .card-front .brand-name {
    position: absolute;
    left: 38px;
    top: 128px;
    font-size: 52px;
  }
  .divider {
    position: absolute;
    left: 232px;
    top: 34px;
    width: 2px;
    height: 240px;
    background: var(--ink);
  }
  .details {
    position: absolute;
    left: 262px;
    top: 44px;
  }
  .person-name { font-size: 21px; font-weight: 700; }
  .person-role { font-size: 15px; color: var(--ink-soft); margin-top: 3px; }
  .address { font-size: 14px; color: var(--ink-soft); margin-top: 24px; line-height: 1.35; }
  .contacts { list-style: none; margin-top: 22px; }
  .contacts li {
    display: flex;
    align-items: center;
    gap: 10px;
    font-size: 14px;
    color: var(--ink-soft);
    margin-bottom: 7px;
  }
  .contacts svg { width: 13px; height: 13px; flex: none; }
  /* Back side */
  .card-back {
    display: flex;
    align-items: center;
    justify-content: center;
  }
  .card-back .brand-name { font-size: 96px; }
</style>
</head>
<body>
  <section class="card card-front">
    <div class="brand-name">LUMA</div>
    <div class="divider"></div>
    <div class="details">
      <div class="person-name">Marcus Hollen</div>
      <div class="person-role">Managing Director</div>
      <div class="address">482 Alder Row, Suite<br>Dorval MA 0173</div>
      <ul class="contacts">
        <li>
          <svg viewBox="0 0 13 13"><rect width="13" height="13" rx="2" fill="#fff"/><path d="M4 3.2l1.3 0 .6 1.8-.9.7c.5 1 1.2 1.7 2.2 2.2l.7-.9 1.8.6v1.3c0 .4-.3.7-.7.7C5.9 9.6 3.4 7.1 3.3 3.9c0-.4.3-.7.7-.7z" fill="#141414"/></svg>
          (318) 4207265518
        </li>
        <li>
          <svg viewBox="0 0 13 13"><rect width="13" height="13" rx="2" fill="#fff"/><circle cx="6.5" cy="6.5" r="3.6" fill="none" stroke="#141414" stroke-width="1"/><path d="M2.9 6.5h7.2M6.5 2.9c-1.4 2-1.4 5.2 0 7.2M6.5 2.9c1.4 2 1.4 5.2 0 7.2" fill="none" stroke="#141414" stroke-width=".8"/></svg>
          www.lumadrift.com
        </li>
        <li>
          <svg viewBox="0 0 13 13"><rect width="13" height="13" rx="2" fill="#fff"/><rect x="2.8" y="4" width="7.4" height="5" fill="none" stroke="#141414" stroke-width="1"/><path d="M2.8 4l3.7 2.8L10.2 4" fill="none" stroke="#141414" stroke-width="1"/></svg>
          info@lumadrift.com
        </li>
      </ul>
    </div>
  </section>
  <section class="card card-back">
    <div class="brand-name">LUMA</div>
  </section>
</body>
</html>
```